KorvaNest - Home Income and Business Resources Platform

I am looking for a website template for a multi-purposed website. This website will feature:

1.) Website Directory with Ratings & comments on listings
2.) Company Blog
3.) Homepage with Content (see files for homepage mock)

I would like the Design to have a default width 1170px (wider then normal)

Of course I am looking for Pages for Listings to be designed.

Great looking BLOG Layout: http://journal.plimworks.example/html/blog.html

I would like 4 Versions of a Website Directory Listing "Box"
1.) Basic Listing Box
2.) Sponsored Listing Box
3.) Recommended Listing Box
4.) Stay Away From Listing Box

Information on the Listing Page (Like on a Category Page)
Site Name, Site URL, Website Image, # of Views, Rating and # of Comments

Information on the Listing Details Page:
Same as ABOVE + About website Description, Vornic Score, Category Information

Decent looking examples is here: https://samples.trevolin.example/directory/computers/ and http://www.zqrankhub.example/.

I will include some sketches and screenshots of things I like/looking for. As designers,you have creative freedom and are encouraged to show this. This is Phase one of this project and winning designer is guaranteed to have future work for this project.

Target Market(s)

Directory, business, websites

Industry/Entity Type

Business

Coding

Coded - Design and coding required

Number of Pages Required

5+ page

Font styles to use
Sans Serif

Colors

Designer to choose colors to be used in the design.

Requirements
Must have
• Professional yet clean look. The use of Icons & images
• Unique Look
Should not have
• Any exact copies of any examples I provided

```html
<!DOCTYPE html>
<html lang="en">
<head>
<meta charset="utf-8">
<title>KorvaNest – Home Income &amp; Business Resources</title>
<link rel="stylesheet" href="https://fonts.googleapis.com/css2?family=Cabin:wght@500;600;700&family=Open+Sans:wght@400;600;700&display=swap">
<style>
  :root{
    --orange:#f08a2c;
    --navy:#2d3b57;
    --ink:#2a2a2a;
    --text:#666;
    --white:#fff;
    --line:rgba(255,255,255,.25);
    --tile-border:#dcdcdc;
    --footer:#1a1a1a;
  }
  *{box-sizing:border-box;margin:0;padding:0}
  html,body{width:1200px;height:951px;overflow:hidden}
  body{position:relative;font-family:"Open Sans",sans-serif;color:var(--text);background:#2b3346}
  .backdrop{position:absolute;inset:0;
    background:linear-gradient(180deg,rgba(45,59,87,.95) 0%,rgba(52,60,78,.85) 20%,rgba(70,66,70,.8) 55%,rgba(40,38,36,.92) 80%,rgba(30,32,28,1) 93%)}
  .top-rule{position:absolute;left:0;top:0;width:100%;height:3px;background:var(--orange)}
  .site-header{position:absolute;left:0;top:3px;width:100%;height:89px;border-bottom:1px solid var(--line)}
  .brand{position:absolute;left:97px;top:29px;font-family:"Cabin",sans-serif;font-weight:700;font-size:23px;color:var(--white);letter-spacing:.2px}
  .main-nav{position:absolute;left:330px;top:34px;display:flex;gap:31px;font-family:"Cabin",sans-serif;font-weight:600;font-size:15px;color:var(--white)}
  .search-icon{position:absolute;left:986px;top:36px}
  .login{position:absolute;left:1021px;top:24px;width:80px;height:35px;border:1px solid rgba(255,255,255,.6);display:flex;align-items:center;justify-content:center;gap:6px;font-family:"Cabin",sans-serif;font-weight:600;font-size:15px;color:var(--orange)}

  .about{position:absolute;left:99px;top:171px;width:759px;height:246px;background:#f4f2f1;border:3px solid var(--white)}
  .about-photo{position:absolute;left:0;top:0;width:320px;height:100%;background:linear-gradient(120deg,#c9b8a8 0%,#d9c7bc 40%,#ece6e2 100%)}
  .about-body{position:absolute;left:327px;top:24px;width:400px}
  .about h1{font-family:"Cabin",sans-serif;font-weight:600;font-size:22px;color:var(--ink)}
  .about h2{font-weight:600;font-size:15px;color:var(--orange);margin-top:9px;white-space:nowrap}
  .about p{font-size:12px;line-height:22.3px;margin-top:6px;color:#666}
  .btn-outline{display:inline-flex;align-items:center;justify-content:center;width:94px;height:32px;border:1px solid #999;color:var(--orange);font-weight:700;font-size:12px;margin-top:14px}

  .card{position:absolute;top:446px;width:238px;height:349px;background:var(--white);border:3px solid var(--white);text-align:center}
  .card-photo{width:100%;height:137px}
  .card-icon{position:absolute;left:50%;top:102px;width:68px;height:68px;margin-left:-34px;border-radius:50%;background:#f4f4f4;display:flex;align-items:center;justify-content:center}
  .card h3{font-family:"Cabin",sans-serif;font-weight:500;font-size:18.5px;line-height:26px;color:var(--ink);margin-top:40px}
  .card p{font-size:12px;line-height:22px;color:#666;margin:10px 4px 0}
  .btn-solid{position:absolute;left:50%;margin-left:-52px;top:330px;width:104px;height:31px;background:var(--orange);border:1px solid var(--white);color:var(--white);font-weight:700;font-size:12.5px;display:flex;align-items:center;justify-content:center}

  .sponsored{position:absolute;left:887px;top:171px;width:214px;height:390px;background:var(--white)}
  .sponsored h4{height:50px;background:var(--orange);color:var(--white);font-family:"Cabin",sans-serif;font-weight:700;font-size:21px;padding:11px 0 0 21px}
  .tile{position:absolute;width:91px;height:55px;border:1px solid var(--tile-border);display:flex;align-items:center;justify-content:center}
  .tile span{display:block;width:56px;height:16px;background:#d8d8d8;border-radius:2px}

  .ad{position:absolute;left:887px;top:597px;width:214px;height:214px;border:3px solid var(--white);background:linear-gradient(180deg,#f1e8d6 0%,#e9dcc1 75%,#b7552a 88%,#8a3a1c 100%)}

  .site-footer{position:absolute;left:0;top:883px;width:100%;height:68px;background:var(--footer);display:flex;align-items:center;justify-content:center;color:#eee;font-size:12.5px}
</style>
</head>
<body>
  <div class="backdrop" role="img" aria-label="Evening photo of a large two-storey suburban house with a lawn, darkened as a background"></div>
  <div class="top-rule"></div>

  <header class="site-header">
    <div class="brand">KORVANEST</div>
    <nav class="main-nav">
      <span>HOME</span><span>ABOUT US</span><span>RESOURCES</span><span>BUSINESS DIRECTORY</span><span>NEWS</span><span>CONTACT</span>
    </nav>
    <svg class="search-icon" width="15" height="15" viewBox="0 0 16 16"><circle cx="6.5" cy="6.5" r="5" fill="none" stroke="#fff" stroke-width="2.2"/><line x1="10.3" y1="10.3" x2="14.5" y2="14.5" stroke="#fff" stroke-width="2.6" stroke-linecap="round"/></svg>
    <div class="login">
      <svg width="11" height="13" viewBox="0 0 11 13"><rect x="0.5" y="5.5" width="10" height="7" rx="1" fill="#f08a2c"/><path d="M2.7 5.5V3.8a2.8 2.8 0 0 1 5.6 0v1.7" fill="none" stroke="#f08a2c" stroke-width="1.6"/></svg>
      LOGIN
    </div>
  </header>

  <section class="about">
    <div class="about-photo" role="img" aria-label="Smiling couple sitting together in front of a laptop"></div>
    <div class="about-body">
      <h1>ABOUT KORVANEST</h1>
      <h2>We are Home Income &amp; Business resources directory.</h2>
      <p>At vero eos et accusamus et iusto odio dignissimos ducimus qui bland itiis praesentium voluptatum deleniti atque corrupti quos dolores etqu as molestias excepturi sint occaecati cupiditate non provident, simique sunt in culpa qui officia deserunt moll.</p>
      <span class="btn-outline">READ MORE</span>
    </div>
  </section>

  <article class="card" style="left:99px">
    <div class="card-photo" role="img" aria-label="Small red-roofed house model, keys and a pen on paperwork" style="background:linear-gradient(135deg,#e9e6e6,#d2cccc 60%,#bdb5b0)"></div>
    <div class="card-icon">
      <svg width="38" height="34" viewBox="0 0 38 34"><path d="M19 3 3 17h5v14h8v-9h6v9h8V17h5z" fill="#f08a2c"/><rect x="26" y="5" width="4" height="8" fill="#f08a2c"/></svg>
    </div>
    <h3>Home Income<br>Resource Directory</h3>
    <p>Find what you need, when you need it.The KorvaNest website directory is your one-stop pit for anything</p>
    <span class="btn-solid">READ MORE</span>
  </article>

  <article class="card" style="left:359px">
    <div class="card-photo" role="img" aria-label="Two people pointing at papers and a tablet on a sunny desk" style="background:linear-gradient(135deg,#c9a27a,#e8d7c0 50%,#4a4038)"></div>
    <div class="card-icon">
      <svg width="38" height="32" viewBox="0 0 38 32"><path d="M4 12h6l16-9v26L10 20H4z" fill="#f08a2c"/><path d="M10 20l3 9h5l-3-9z" fill="#f08a2c"/><path d="M30 11q4 5 0 10" fill="none" stroke="#f08a2c" stroke-width="2.5"/></svg>
    </div>
    <h3>Advertising<br>Benefits</h3>
    <p>Everyone needs to advertise and we know just how to get your offer out to the right people. We have many</p>
    <span class="btn-solid">READ MORE</span>
  </article>

  <article class="card" style="left:620px">
    <div class="card-photo" role="img" aria-label="Hand touching a rising chart on a blue screen" style="background:linear-gradient(135deg,#2c4f86,#6f8fbe 55%,#cfd8e6)"></div>
    <div class="card-icon">
      <svg width="40" height="28" viewBox="0 0 40 28"><rect x="1.5" y="2.5" width="37" height="23" rx="1" fill="none" stroke="#f08a2c" stroke-width="3"/><rect x="6" y="7" width="28" height="14" fill="#f08a2c"/><circle cx="20" cy="14" r="5.5" fill="#fff"/><text x="20" y="18" text-anchor="middle" font-family="Open Sans,sans-serif" font-weight="700" font-size="10" fill="#f08a2c">1</text></svg>
    </div>
    <h3>Earning With<br>KorvaNest</h3>
    <p>Join KorvaNest and start earning money. When you share KorvaNest and lock in an advertiser or premium listing,</p>
    <span class="btn-solid">READ MORE</span>
  </article>

  <aside class="sponsored">
    <h4>SPONSORED</h4>
    <div class="tile" style="left:10px;top:75px"><span></span></div>
    <div class="tile" style="left:112px;top:75px"><span></span></div>
    <div class="tile" style="left:10px;top:152px"><span></span></div>
    <div class="tile" style="left:112px;top:152px"><span></span></div>
    <div class="tile" style="left:10px;top:229px"><span></span></div>
    <div class="tile" style="left:112px;top:229px"><span></span></div>
    <div class="tile" style="left:10px;top:306px"><span></span></div>
    <div class="tile" style="left:112px;top:306px"><span></span></div>
  </aside>

  <div class="ad" role="img" aria-label="Home equity advertisement with a house outline drawn from tools"></div>

  <footer class="site-footer">Copyright © 2017. KorvaNest. All Rights Reserved.</footer>
</body>
</html>
```